mechanical repair shop

our shop repairs light and medium duty trucks

we sell tires , do oil changes, engine and transmissions
vehicle accessories, alignments, brakes , exhaust, all major and minor repairs.
Updates

if you would like to get a hold of me email: milo.hensworth@quarrytide.net tel: 1-780-555-0148

Target Market(s)

light and medium duty trucks and cars

Industry/Entity Type

Shop

Colors
f37122

Requirements
Must have
• visual sales displays
Nice to have
• pictures

```html
<!DOCTYPE html>
<html lang="en">
<head>
<meta charset="utf-8">
<title>Ridgeline Truck Services – Flyer</title>
<link rel="stylesheet" href="https://fonts.googleapis.com/css2?family=Oswald:wght@400;500;600&family=Montserrat:wght@400;500&display=swap">
<style>
  :root{
    --orange:#f37122;
    --black:#0d0d0d;
    --white:#ffffff;
    --ink:#222222;
    --stage:#333335;
  }
  *{box-sizing:border-box;margin:0;padding:0}
  html,body{width:1200px;height:900px;overflow:hidden;background:var(--stage)}
  .flyer{position:absolute;left:300px;top:24px;width:600px;height:852px;overflow:hidden;background:var(--black);box-shadow:0 12px 30px rgba(0,0,0,.45)}
  .flyer-shapes{position:absolute;inset:0}
  .brand{position:absolute;left:370px;top:20px;width:140px;height:140px;border-radius:50%;background:var(--black);display:flex;align-items:center;justify-content:center;text-align:center}
  .brand-name{font-family:'Oswald',sans-serif;font-weight:500;font-size:17px;line-height:1.15;color:var(--white);letter-spacing:.5px}
  .headline{position:absolute;right:40px;top:234px;text-align:right;font-family:'Oswald',sans-serif;font-weight:600;font-size:25px;line-height:1.15;color:var(--white);text-transform:uppercase;letter-spacing:-.3px}
  .headline .accent{color:var(--orange)}
  .services{position:absolute;left:300px;top:342px;width:290px}
  .services-title{font-family:'Oswald',sans-serif;font-weight:500;font-size:29px;color:var(--orange);margin-bottom:10px}
  .service-list{list-style:none;font-family:'Montserrat',sans-serif;font-size:11px;color:var(--ink)}
  .service-list li{position:relative;padding-left:20px;height:21.5px;line-height:21.5px;white-space:nowrap}
  .service-list li::before{content:"";position:absolute;left:0;top:5px;width:10px;height:10px;border:1.4px solid var(--orange);border-radius:50%}
  .service-list li::after{content:"";position:absolute;left:4px;top:7px;width:3px;height:5px;border-right:1.6px solid var(--orange);border-bottom:1.6px solid var(--orange);transform:rotate(45deg)}
  .about{position:absolute;left:30px;top:552px;width:266px;font-family:'Montserrat',sans-serif;font-size:9.8px;line-height:1.45;color:var(--ink);text-align:justify}
  .website{position:absolute;left:70px;top:810px;font-family:'Oswald',sans-serif;font-size:15px;color:var(--white);letter-spacing:.3px}
  .contact{position:absolute;right:34px;top:752px;text-align:right;font-family:'Oswald',sans-serif}
  .contact-lead{font-size:17px;color:var(--orange)}
  .contact-phone{font-size:33px;font-weight:400;color:var(--white);display:flex;align-items:center;gap:8px;line-height:1.1}
  .contact-phone svg{width:24px;height:24px}
</style>
</head>
<body>
<main class="flyer">
  <svg class="flyer-shapes" viewBox="0 0 600 852" width="600" height="852">
    <defs>
      <linearGradient id="truckTone" x1="0" y1="0" x2="1" y2="1">
        <stop offset="0" stop-color="#f4f4f4"/>
        <stop offset=".6" stop-color="#d9d9d9"/>
        <stop offset="1" stop-color="#555"/>
      </linearGradient>
      <linearGradient id="tireTone" x1="0" y1="0" x2="1" y2="1">
        <stop offset="0" stop-color="#8a8f96"/>
        <stop offset=".5" stop-color="#2b2b2d"/>
        <stop offset="1" stop-color="#6c6f74"/>
      </linearGradient>
      <linearGradient id="oilTone" x1="0" y1="0" x2="1" y2="1">
        <stop offset="0" stop-color="#b9bcc0"/>
        <stop offset=".5" stop-color="#c98a1c"/>
        <stop offset="1" stop-color="#3a3a3c"/>
      </linearGradient>
    </defs>
    <path class="top-wave" d="M210 0 H600 V150 C500 190 390 210 300 214 C270 150 240 70 210 0 Z" fill="#fff"/>
    <path class="top-stripe" d="M300 214 C390 210 500 190 600 150 V164 C505 206 400 226 318 228 Z" fill="var(--orange)"/>
    <rect x="22" y="62" width="280" height="165" rx="6" fill="url(#truckTone)" role="img" aria-label="White box truck photo"/>
    <path class="body-panel" d="M0 420 C120 360 330 320 600 318 V720 C420 740 240 740 0 730 Z" fill="#fff"/>
    <path class="body-stripe" d="M60 395 C190 340 380 325 520 320 C360 336 200 360 90 420 Z" fill="var(--orange)"/>
    <path class="side-swoosh" d="M0 440 C20 420 40 405 60 398 C30 440 22 480 30 520 L0 532 Z" fill="var(--orange)"/>
    <circle cx="150" cy="440" r="102" fill="var(--orange)"/>
    <circle cx="150" cy="440" r="96" fill="#fff"/>
    <circle cx="150" cy="440" r="92" fill="url(#tireTone)" role="img" aria-label="Mechanic mounting a tire photo"/>
    <path class="bottom-stripe" d="M0 728 C160 772 330 770 600 712 V728 C330 786 160 788 0 744 Z" fill="var(--orange)"/>
    <path class="bottom-band" d="M0 744 C160 788 330 786 600 728 V852 H0 Z" fill="var(--black)"/>
    <circle cx="300" cy="772" r="66" fill="var(--orange)"/>
    <circle cx="300" cy="772" r="61" fill="#fff"/>
    <circle cx="300" cy="772" r="57" fill="url(#oilTone)" role="img" aria-label="Engine oil being poured photo"/>
  </svg>

  <div class="brand"><span class="brand-name">RIDGELINE<br>Truck Services Ltd.</span></div>

  <h1 class="headline">Your complete <span class="accent">light</span><br><span class="accent">medium duty truck</span><br>repair facility</h1>

  <section class="services">
    <h2 class="services-title">Services We Offer:</h2>
    <ul class="service-list">
      <li>Factory recommended service/maintenance</li>
      <li>Oil change</li>
      <li>Fuel system repair and maintenance</li>
      <li>Battery system diagnosis &amp; repair</li>
      <li>Check engine light</li>
      <li>Electrical problems</li>
      <li>Engine performance</li>
      <li>Exhaust problems</li>
      <li>Tires</li>
      <li>30/60/90 K mileage maintenance services</li>
      <li>Cooling system repair and maintenance</li>
      <li>Air conditioning / heating repair</li>
      <li>Brake system</li>
      <li>Steering &amp; suspension</li>
    </ul>
  </section>

  <p class="about">Ridgeline Truck Services Ltd. has set up and successfully operates a complete equipment repair facility. First set up to be a dedicated repair shop for a single large client, Ridgeline has now expanded to include all manner of clients with diverse equipment needs. With Journeyman and Apprentice HD mechanics available 24 hours a day our facility is ready to handle all of your equipment needs. We are an 'approved' repair facility for a growing list of equipment manufacturers including: Northcrane, Halvex, Liftora, Bramwell, Skyforge etc.</p>

  <p class="website">www.ridgelinetruck.com</p>

  <div class="contact">
    <p class="contact-lead">Call us for more information</p>
    <p class="contact-phone">
      <svg viewBox="0 0 24 24" aria-hidden="true"><path fill="#fff" d="M6.6 10.8c1.4 2.8 3.8 5.1 6.6 6.6l2.2-2.2c.3-.3.7-.4 1-.2 1.1.4 2.3.6 3.6.6.6 0 1 .4 1 1V20c0 .6-.4 1-1 1C10.6 21 3 13.4 3 4c0-.6.4-1 1-1h3.5c.6 0 1 .4 1 1 0 1.3.2 2.5.6 3.6.1.3 0 .7-.2 1z"/></svg>
      780 555 0192
    </p>
  </div>
</main>
</body>
</html>
```